Building company buisness cards

We are looking for a sharp modern new look for our business cards.
We are a New Zealand based company that specialises in house and land packages.
We have attached a photo of the current logo and would like to see if it can be improved somehow if needed.
We are open to any colours but we have chosen green at this stage.
Feel free to change the font and make the logo smarter looking.
Play with the colours and see what looks best.

We want a card that looks so good know one will want to throw it away!

Target Market(s)

Home buyers

Industry/Entity Type

Building

Contact Information for Business Card

Derek Tolvane
0217394062
dtolvane@quillmarkhomesteads.co.nz
quillmarkhomesteads.co.nz

Font styles to use
Serif
Sans Serif

Colors

Designer to choose colors to be used in the design.

Requirements
Must have
• Logo and company name on one side, details on the other side
Nice to have
• Color codes for the original green are HEX #4a8028, RGB(74,128,40), CMYK(42,0,69,50)
• Round corners, Raised and/or spot UV

```html
<!DOCTYPE html>
<html lang="en">
<head>
<meta charset="utf-8">
<title>Quillmark Homesteads – Business Cards</title>
<link href="https://fonts.googleapis.com/css2?family=Lato:wght@400;700;900&display=swap" rel="stylesheet">
<style>
  :root {
    --brand-green: #4a8028;
    --card-white: #ffffff;
    --ink-grey: #4a4a4a;
    --rule-grey: #b5b5b5;
    --backdrop: #e6e7e6;
  }
  * { box-sizing: border-box; margin: 0; padding: 0; }
  html, body {
    width: 1200px; height: 900px; overflow: hidden;
    background: var(--backdrop);
    font-family: "Lato", "Helvetica Neue", Arial, sans-serif;
  }
  .sheet {
    width: 1200px; height: 900px;
    display: flex; flex-direction: column; align-items: center; justify-content: center;
    gap: 44px;
  }
  .card {
    position: relative;
    width: 600px; height: 343px;
    background: var(--card-white);
    border-radius: 6px;
    overflow: hidden;
    box-shadow: 0 2px 10px rgba(0,0,0,0.12);
    display: flex; flex-direction: column; align-items: center; justify-content: center;
  }
  .card__band {
    position: absolute; left: 0; right: 0; bottom: 0;
    height: 12px; background: var(--brand-green);
  }
  /* front */
  .wordmark {
    display: flex; align-items: center; gap: 12px;
    margin-top: -14px;
  }
  .wordmark__square {
    width: 30px; height: 30px; background: var(--brand-green); border-radius: 4px;
  }
  .wordmark__name {
    font-weight: 900; font-size: 38px; color: var(--brand-green);
    letter-spacing: -0.5px; line-height: 1;
  }
  .front__rule {
    width: 60px; height: 1px; background: var(--rule-grey); margin-top: 18px;
  }
  /* back */
  .holder-name {
    font-weight: 700; font-size: 21px; color: var(--brand-green);
    letter-spacing: 0.3px; text-transform: uppercase;
    margin-top: 10px;
  }
  .icon-row {
    display: flex; align-items: center; gap: 6px; margin-top: 10px;
  }
  .icon-row__rule { width: 40px; height: 1px; background: var(--rule-grey); }
  .icon-row__rule--long { width: 48px; }
  .icon-tile {
    width: 22px; height: 22px; border-radius: 5px; background: var(--brand-green);
    display: flex; align-items: center; justify-content: center;
  }
  .contact-list {
    list-style: none; text-align: center; margin-top: 6px;
    color: var(--ink-grey); font-size: 16.5px; line-height: 1.25;
  }
</style>
</head>
<body>
<main class="sheet">
  <section class="card card--front" aria-label="Card front">
    <div class="wordmark">
      <span class="wordmark__square" aria-hidden="true"></span>
      <span class="wordmark__name">Quillmark Homesteads</span>
    </div>
    <div class="front__rule"></div>
    <div class="card__band"></div>
  </section>

  <section class="card card--back" aria-label="Card back">
    <h1 class="holder-name">Derek Tolvane</h1>
    <div class="icon-row">
      <span class="icon-row__rule icon-row__rule--long"></span>
      <span class="icon-tile" aria-label="Phone">
        <svg width="13" height="13" viewBox="0 0 24 24"><path fill="#fff" d="M6.6 10.8a15 15 0 0 0 6.6 6.6l2.2-2.2a1 1 0 0 1 1-.25 11.4 11.4 0 0 0 3.6.57 1 1 0 0 1 1 1V20a1 1 0 0 1-1 1A17 17 0 0 1 3 4a1 1 0 0 1 1-1h3.5a1 1 0 0 1 1 1c0 1.25.2 2.45.57 3.57a1 1 0 0 1-.25 1z"/></svg>
      </span>
      <span class="icon-tile" aria-label="Email">
        <svg width="13" height="13" viewBox="0 0 24 24"><rect x="2" y="5" width="20" height="14" rx="1.5" fill="#fff"/><path d="M3 6l9 7 9-7" fill="none" stroke="#4a8028" stroke-width="1.8"/></svg>
      </span>
      <span class="icon-tile" aria-label="Website">
        <svg width="13" height="13" viewBox="0 0 24 24"><g fill="none" stroke="#fff" stroke-width="2"><circle cx="12" cy="12" r="9"/><ellipse cx="12" cy="12" rx="4" ry="9"/><path d="M3 12h18"/></g></svg>
      </span>
      <span class="icon-row__rule icon-row__rule--long"></span>
    </div>
    <ul class="contact-list">
      <li>0217394062</li>
      <li>dtolvane@quillmarkhomesteads.co.nz</li>
      <li>www.quillmarkhomesteads.co.nz</li>
    </ul>
    <div class="card__band"></div>
  </section>
</main>
</body>
</html>
```